Fitness website

Website for a fitness brand (see attached specs). Design needs to be modern and vibrant with CTAs on every page. We will provide logos, images, etc but for now user placeholder text and images. For now use the name 'Corvane Athletics' as the name to use on the design. The goal of this site is to either get people to join the gym (5 physical locations across the US); buy an online program; buy merch or supplements or sign up for the newsletter. Pleas use images from this foldeR: https://filebarn.example/share/folders/8QwTz41mKpLrXv93NdYe7HsaBuJ0Cf2_R?usp=sharing

We will be coding this in ReactNative. Lots more work for the winner as well, this is a 1st project for us.

Target Market(s)

fitness enthusiats

Industry/Entity Type

fitness, health, wellness

Number of Pages Required

5+ page

Font styles to use
Other font styles liked:
• Lato

Colors
0054AA
0677BA
7BADD7
CADEEF
E8F1F8
0094D4
00A9DD
6FCCEA
C7EBF8
E9F6FB
00AB8E
00BBA5
67D7C9
C6EFE9
E9F9F6
EE7325
F08F49
F5BC92
FAE3D3
FDF4ED

Requirements
Must have
• must be reactive. most people will view it first on mobile
Nice to have
• video in hero section of top of home page

```html
<!DOCTYPE html>
<html lang="en">
<head>
<meta charset="utf-8">
<title>Corvane Athletics</title>
<link href="https://fonts.googleapis.com/css2?family=Lato:wght@300;400;700;900&display=swap" rel="stylesheet">
<style>
:root{
  --blue:#0054AA;
  --blue-mid:#0677BA;
  --sky:#0094D4;
  --green:#0E9A4A;
  --green-dark:#0B7A3A;
  --ink:#1d1d1d;
  --muted:#777;
  --light:#f4f6f8;
  --footer:#0b0b0b;
  --white:#fff;
  --gold:#f5b400;
}
*{box-sizing:border-box;margin:0;padding:0}
html,body{width:1200px;height:3884px;overflow:hidden}
body{font-family:'Lato',sans-serif;color:var(--ink);background:var(--white);position:relative}
a{color:inherit;text-decoration:none}
.container{width:960px;margin:0 auto;position:relative}
.btn{display:inline-flex;align-items:center;gap:10px;font-weight:700;font-size:13px;letter-spacing:.5px;padding:12px 26px;border-radius:24px;text-transform:uppercase}
.btn-green{background:var(--green);color:var(--white)}
.btn-white{background:var(--white);color:var(--green)}
.btn .arr{font-size:15px}
.section-title{text-align:center;font-size:34px;font-weight:400;letter-spacing:.5px}
.section-title b{font-weight:900}
.section-title::after{content:"";display:block;width:50px;height:3px;background:var(--sky);margin:10px auto 0}
.ph{display:block}

/* header */
.site-header{height:70px;background:var(--white);position:relative}
.brand{position:absolute;left:140px;top:22px;font-weight:900;font-size:22px;color:var(--blue);letter-spacing:.5px}
.util{position:absolute;right:140px;top:6px;display:flex;gap:24px;font-size:12px;color:#444}
.util span::before{content:"";display:inline-block;width:7px;height:7px;border-radius:50%;background:var(--blue);margin-right:6px}
.main-nav{position:absolute;right:140px;top:38px;display:flex;gap:30px;font-size:13px;font-weight:700;color:#333}
.main-nav .active{color:var(--blue);border-bottom:2px solid var(--blue);padding-bottom:4px}

/* hero */
.hero{height:458px;position:relative;color:var(--white);text-align:center}
.hero .ph{position:absolute;inset:0;background:linear-gradient(180deg,#3a4046 0%,#2b2f33 50%,#45352e 100%)}
.hero-inner{position:relative;padding-top:110px}
.hero h1{font-size:50px;font-weight:900;letter-spacing:1px}
.hero p{font-size:19px;font-weight:700;margin-top:8px}
.hero .btn{margin-top:26px}
.play{margin-top:90px;display:inline-flex;align-items:center;gap:10px;font-weight:900;font-size:17px}

/* programs */
.programs{height:512px;padding-top:48px;position:relative}
.prog-grid{display:grid;grid-template-columns:repeat(3,290px);column-gap:45px;margin-top:34px}
.prog-img{height:155px}
.prog-col h3{font-size:17px;font-weight:700;margin:10px 0 6px}
.prog-col p{font-size:12px;color:var(--muted);line-height:1.5}
.more{display:inline-flex;align-items:center;gap:6px;font-size:11px;font-weight:900;margin-top:10px}
.more i{width:18px;height:18px;border-radius:50%;background:var(--green);display:inline-block}
.carousel-arrow{position:absolute;top:230px;font-size:28px;color:#333}
.dots{display:flex;gap:7px;justify-content:center;margin-top:18px}
.dots i{width:8px;height:8px;border-radius:50%;background:#ccc}
.dots i.on{background:var(--blue)}

/* about */
.about{height:490px;background:var(--light);padding-top:60px}
.about .container{display:flex;gap:60px}
.about-media{position:relative;width:440px;height:350px}
.about-media .frame{position:absolute;left:-20px;top:-20px;width:110px;height:110px;border-left:8px solid var(--green);border-top:8px solid var(--green)}
.about-media .frame.b{left:auto;top:auto;right:-20px;bottom:-20px;border:0;border-right:8px solid var(--green);border-bottom:8px solid var(--green)}
.about-media .ph{position:absolute;inset:0;background:linear-gradient(135deg,#3b3b3b,#7a5a44 60%,#2a2a2a)}
.about-text{width:460px;padding-top:60px}
.about-text h2{font-size:34px;font-weight:400}
.about-text h2 b{font-weight:900}
.about-text h2::after{content:"";display:block;width:50px;height:3px;background:var(--sky);margin-top:10px}
.about-text p{font-size:13px;color:var(--muted);line-height:1.6;margin-top:16px}
.about-text .btn{margin-top:26px}

/* ready */
.ready{height:260px;position:relative;color:var(--white);text-align:center}
.ready .ph{position:absolute;inset:0;background:linear-gradient(90deg,#0c8a40,#14a552 50%,#0c8a40)}
.ready-inner{position:relative;padding-top:52px}
.ready h2{font-size:34px;font-weight:400}
.ready h2 b{font-weight:900}
.ready p{font-size:14px;line-height:1.5;width:900px;margin:18px auto 0}
.ready .btn{margin-top:28px}

/* locations */
.locations{height:420px;padding-top:50px;position:relative}
.loc-grid{display:grid;grid-template-columns:repeat(4,225px);gap:20px;margin-top:36px}
.loc-card{background:var(--white);box-shadow:0 2px 8px rgba(0,0,0,.12)}
.loc-card .ph{height:155px}
.loc-card span{display:block;text-align:center;font-size:13px;font-weight:700;padding:10px 0}
.loc-cta{text-align:center;margin-top:22px}

/* stories */
.stories{height:350px;padding-top:20px;position:relative;overflow:hidden}
.stories .section-title b{font-weight:900}
.story-row{display:flex;gap:28px;justify-content:center;margin-top:32px}
.story{width:290px;background:var(--white);box-shadow:0 2px 10px rgba(0,0,0,.12);padding:18px 20px}
.story.fade{opacity:.35;flex-shrink:0}
.stars{color:var(--gold);letter-spacing:3px;font-size:15px}
.story p{font-size:12px;color:var(--muted);line-height:1.5;margin-top:8px}
.who{display:flex;align-items:center;gap:12px;margin-top:14px}
.who .ph{width:44px;height:44px;border-radius:50%;background:#b9a596}
.who b{font-size:14px;display:block}
.who small{font-size:11px;color:var(--green)}

/* newsletter + footer */
.news-wrap{position:relative;height:214px}
.news-wrap::after{content:"";position:absolute;left:0;right:0;bottom:0;height:100px;background:var(--footer)}
.newsletter{position:relative;z-index:1;width:960px;height:200px;margin:0 auto;background:linear-gradient(90deg,#0b63b0,#1b7cc6);color:var(--white);text-align:center;padding-top:30px}
.newsletter h2{font-size:32px;font-weight:400}
.newsletter h2 b{font-weight:900}
.newsletter p{font-size:13px;margin-top:10px}
.signup{width:440px;height:40px;margin:22px auto 0;background:var(--white);border-radius:20px;display:flex;align-items:center;justify-content:space-between;padding-left:20px;font-size:12px;color:#999}
.signup span.b{background:var(--green);color:var(--white);font-weight:900;height:40px;line-height:40px;padding:0 30px;border-radius:20px}
.site-footer{background:var(--footer);color:#ddd;height:970px;padding-top:20px}
.foot-cols{display:grid;grid-template-columns:repeat(4,1fr);gap:30px}
.foot-cols h4{font-size:14px;font-weight:900;color:var(--white);margin-bottom:14px;letter-spacing:.5px}
.foot-cols li{list-style:none;font-size:13px;margin-bottom:9px}
.foot-cols li::before{content:"›";color:var(--green);margin-right:8px;font-weight:900}
.contact li::before{content:"";display:inline-block;width:14px;height:14px;border-radius:50%;background:var(--green);vertical-align:middle;margin-right:10px}
.foot-bottom{text-align:center;margin-top:70px}
.foot-bottom .name{font-size:26px;font-weight:900;color:var(--sky)}
.foot-bottom p{font-size:12px;color:#aaa;margin-top:8px}
.socials{display:flex;gap:14px;justify-content:center;margin-top:18px}
.socials i{width:34px;height:34px;border-radius:50%;background:#333}
.socials i.on{background:var(--green)}
</style>
</head>
<body>

<header class="site-header">
  <a class="brand" href="#">CORVANE ATHLETICS</a>
  <div class="util"><span>Members</span><span>Shop</span><span>Search</span></div>
  <nav class="main-nav">
    <a class="active">HOME</a><a>ABOUT</a><a>PROGRAMS</a><a>AFFILIATES</a><a>BLOG</a><a>LOCATIONS</a><a>CONTACT</a>
  </nav>
</header>

<section class="hero">
  <div class="ph" role="img" aria-label="Gym class members doing floor exercises in a training hall"></div>
  <div class="hero-inner">
    <h1>WELCOME TO CORVANE ATHLETICS</h1>
    <p>Lorem ipsum dolor sit amet, consectetur adipiscing elit, sed do eiusmod tempor incididunt.</p>
    <a class="btn btn-green">Join the Gym <span class="arr">→</span></a><br>
    <span class="play">
      <svg width="26" height="26" viewBox="0 0 26 26"><circle cx="13" cy="13" r="13" fill="#fff"/><path d="M10 8 L18 13 L10 18Z" fill="#222"/></svg>
      PLAY NOW
    </span>
  </div>
</section>

<section class="programs">
  <h2 class="section-title">OUR <b>PROGRAMS</b></h2>
  <span class="carousel-arrow" style="left:80px">‹</span>
  <span class="carousel-arrow" style="right:80px">›</span>
  <div class="container">
    <div class="prog-grid">
      <div class="prog-col">
        <div class="ph prog-img" role="img" aria-label="Group of athletes posing in a gym" style="background:linear-gradient(135deg,#2c2c2c,#6b4a3b)"></div>
        <h3>Masters</h3>
        <p>Sed ut perspiciatis unde omnis iste natus error sit voluptatem accusantium.</p>
        <a class="more"><i></i>LEARN MORE</a>
      </div>
      <div class="prog-col">
        <h3 style="margin-top:0">Functional Fitness</h3>
        <p>Sed ut perspiciatis unde omnis iste natus error sit voluptatem accusantium.</p>
        <a class="btn btn-green" style="margin:12px 0 14px;padding:9px 20px;font-size:11px">Learn More <span class="arr">→</span></a>
        <div class="ph prog-img" role="img" aria-label="Athletes training with kettlebells" style="background:linear-gradient(135deg,#404040,#8a7565)"></div>
      </div>
      <div class="prog-col">
        <div class="ph prog-img" role="img" aria-label="Healthy meal being prepared in a kitchen" style="background:linear-gradient(135deg,#c9d6c2,#e9d9c4)"></div>
        <h3>Nutrition</h3>
        <p>Sed ut perspiciatis unde omnis iste natus error sit voluptatem accusantium.</p>
        <a class="more"><i></i>LEARN MORE</a>
      </div>
    </div>
    <div class="dots"><i class="on"></i><i></i><i></i></div>
  </div>
</section>

<section class="about">
  <div class="container">
    <div class="about-media">
      <span class="frame"></span><span class="frame b"></span>
      <div class="ph" role="img" aria-label="Athlete lifting a heavy weight in the gym"></div>
    </div>
    <div class="about-text">
      <h2><b>ABOUT</b> US</h2>
      <p>Lorem ipsum dolor sit amet, consectetur adipiscing elit, sed do eiusmod tempor incididunt ut labore et dolore magna aliqua ut enim ad minim veniam.</p>
      <p>Sed ut perspiciatis unde omnis iste natus error sit voluptatem accusantium doloremque laudantium, totam rem aperiam, eaque ipsa quae ab illo inventore veritatis et quasi architecto beatae vitae dicta sunt explicabo nemo enim ipsam voluptatem quia voluptas.</p>
      <a class="btn btn-green">Learn More About Us <span class="arr">→</span></a>
    </div>
  </div>
</section>

<section class="ready">
  <div class="ph" role="img" aria-label="Green-tinted gym interior background"></div>
  <div class="ready-inner">
    <h2>READY <b>TO GET STARTED</b></h2>
    <p>Lorem ipsum dolor sit amet, consectetur adipiscing elit, sed do eiusmod tempor incididunt ut labore et dolore magna aliqua ut enim ad minim veniam quis nostrud exercitation ullamco laboris nisi ut aliquip ex ea commodo consequat.</p>
    <a class="btn btn-white">Buy an Online Program <span class="arr">→</span></a>
  </div>
</section>

<section class="locations">
  <h2 class="section-title">OUR <b>BRANCH LOCATIONS</b></h2>
  <span class="carousel-arrow" style="left:80px;top:230px">‹</span>
  <span class="carousel-arrow" style="right:80px;top:230px">›</span>
  <div class="container">
    <div class="loc-grid">
      <div class="loc-card"><div class="ph" role="img" aria-label="San Diego city skyline" style="background:linear-gradient(180deg,#8fc0e8,#3d6c8f)"></div><span>SAN DIEGO (HQ)</span></div>
      <div class="loc-card"><div class="ph" role="img" aria-label="Boston city skyline" style="background:linear-gradient(180deg,#6a8fb8,#2d3f55)"></div><span>BOSTON</span></div>
      <div class="loc-card"><div class="ph" role="img" aria-label="Miami palm trees and hotels" style="background:linear-gradient(180deg,#9fd3f2,#5e9f6a)"></div><span>MIAMI</span></div>
      <div class="loc-card"><div class="ph" role="img" aria-label="Seattle skyline with tower" style="background:linear-gradient(180deg,#a8c8e6,#4d6a80)"></div><span>SEATTLE</span></div>
    </div>
    <div class="loc-cta"><a class="btn btn-green">Explore Now <span class="arr">→</span></a></div>
  </div>
</section>

<section class="stories">
  <h2 class="section-title">REAL STORIES <b>REAL SUCCESS</b></h2>
  <div class="story-row">
    <div class="story fade"><div class="stars">★★★★★</div><p>Lorem ipsum dolor sit amet, consectetur adipiscing elit, sed do eiusmod tempor incididunt ut labore.</p></div>
    <div class="story"><div class="stars">★★★★★</div><p>Lorem ipsum dolor sit amet, consectetur adipiscing elit, sed do eiusmod tempor incididunt ut labore et dolore magna aliqua.</p><div class="who"><span class="ph" role="img" aria-label="Member portrait"></span><div><b>Tobin Marsh</b><small>Lorem ipsum</small></div></div></div>
    <div class="story"><div class="stars">★★★★★</div><p>Lorem ipsum dolor sit amet, consectetur adipiscing elit, sed do eiusmod tempor incididunt ut labore et dolore magna aliqua.</p><div class="who"><span class="ph" role="img" aria-label="Member portrait"></span><div><b>Rhea Lindqvist</b><small>Lorem ipsum</small></div></div></div>
    <div class="story"><div class="stars">★★★★★</div><p>Lorem ipsum dolor sit amet, consectetur adipiscing elit, sed do eiusmod tempor incididunt ut labore et dolore magna aliqua.</p><div class="who"><span class="ph" role="img" aria-label="Member portrait"></span><div><b>Dana Okafor</b><small>Lorem ipsum</small></div></div></div>
    <div class="story fade"><div class="stars">★★★★★</div><p>Lorem ipsum dolor sit amet, consectetur adipiscing elit, sed do eiusmod tempor incididunt ut labore.</p></div>
  </div>
</section>

<div class="news-wrap">
  <section class="newsletter">
    <h2>SIGN UP <b>TO OUR NEWSLETTER</b></h2>
    <p>Lorem ipsum dolor sit amet, consectetur adipiscing elit, sed do eiusmod tempor incididunt ut labore et dolore</p>
    <div class="signup"><span>Enter your email</span><span class="b">SIGN UP</span></div>
  </section>
</div>

<footer class="site-footer">
  <div class="container">
    <div class="foot-cols">
      <div><h4>PAGES</h4><ul><li>Home</li><li>About</li><li>Programs</li><li>Affiliates</li><li>Blog</li><li>Locations</li><li>Contact</li></ul></div>
      <div><h4>LINKS</h4><ul><li>Privacy Policy</li><li>Terms and Conditions</li><li>Term of Use</li><li>Site Map</li><li>Join Our Team</li></ul></div>
      <div><h4>SHOP</h4><ul><li>My Account</li><li>Returns &amp; Exchanges</li><li>Shop FAQ</li><li>Tracking Info</li><li>Customer Login</li><li>Shipping Policy</li></ul></div>
      <div class="contact"><h4>CONTACT US</h4><ul><li>+1-555-014-2290</li><li>info@corvaneathletics.com</li><li>48 Larkfield Row, Suite 12, Portvale 97109</li></ul></div>
    </div>
    <div class="foot-bottom">
      <div class="name">CORVANE ATHLETICS</div>
      <p>Copyright 2020 Corvane Athletics | All Rights Reserved</p>
      <div class="socials"><i></i><i class="on"></i><i></i></div>
    </div>
  </div>
</footer>

</body>
</html>
```